Business Card Re-Design/Update

We'd like to update out business cards. I've included our current "Style guide" which has the colour scheme of the organisation in it. I've also included the branding files with logos etc in them.

I've also included a copy of one of our existing cards so that you can see how ugly/dated they look. I'd like a fresh modern corporate look.

Target Market(s)

These are for our clients, potential clients, industry contacts - like all business cards

Contact Information for Business Card

Name
Position
Company Address - Level 1, 47 Fernby Street, Carlow Qld 4072
Direct Phone
mobile
Email
Website -www.korvalit.com.au
Logo

Colors

Designer to choose colors to be used in the design.

Requirements
Must have
• Main Logo
• Cards will need to be editable to be able to personalize them for each new employee.
Nice to have
• The MapOut, ShipWell, KeepSteady would be okay to have if they can be sensibly and professionally added to the look without detracting from the main imagery.
• Maybe they could go on the back of the card? will leave this to your creative discretion as to whether/where they fit.
Should not have
• Should not have decorative or script fonts

```html
<!DOCTYPE html>
<html lang="en">
<head>
<meta charset="utf-8">
<title>Korvalit Business Card</title>
<link href="https://fonts.googleapis.com/css2?family=Roboto:wght@400;500;700&family=Roboto+Condensed:wght@400;700&display=swap" rel="stylesheet">
<style>
  :root{
    --bg:#2b2b2d;
    --card:#f7f7f7;
    --red:#c4252b;
    --band-red:#b3262a;
    --blue:#3a4fa0;
    --ink:#2e2e2e;
    --muted:#555;
    --rule:#cfcfcf;
    --green:#7bb342;
    --sky:#1f8fd6;
    --magenta:#c2299a;
    --faint:#f3d4d4;
  }
  *{box-sizing:border-box;margin:0;padding:0}
  html,body{width:1200px;height:911px;overflow:hidden;background:var(--bg)}
  .canvas{position:relative;width:1200px;height:911px;font-family:"Roboto",sans-serif}
  .card{position:absolute;width:540px;height:309px;background:var(--card);overflow:hidden;box-shadow:0 10px 30px rgba(0,0,0,.45)}
  .card--front{left:60px;top:140px}
  .card--back{left:600px;top:462px}

  /* front */
  .brand{position:absolute;left:46px;top:128px;display:flex;align-items:center;gap:10px}
  .brand__mark{width:24px;height:24px;background:var(--red)}
  .brand__name{font-family:"Roboto",sans-serif;font-weight:400;font-size:34px;letter-spacing:-.5px;color:var(--ink);line-height:1}
  .divider{position:absolute;left:262px;top:40px;width:1px;height:200px;background:var(--rule)}
  .details{position:absolute;left:284px;top:40px;width:240px}
  .person__name{font-family:"Roboto Condensed",sans-serif;font-weight:700;font-size:18px;color:var(--red);text-transform:uppercase;letter-spacing:.2px}
  .person__role{font-family:"Roboto Condensed",sans-serif;font-weight:700;font-size:12.5px;color:var(--ink);margin-top:2px}
  .address{font-family:"Roboto Condensed",sans-serif;font-size:12px;color:var(--muted);margin-top:8px;line-height:1.4}
  .contacts{list-style:none;margin-top:10px}
  .contacts li{display:flex;align-items:center;gap:8px;font-family:"Roboto Condensed",sans-serif;font-size:12px;color:var(--muted);line-height:1.55}
  .contacts svg{width:11px;height:11px;flex:none}
  .band{position:absolute;left:0;right:0;bottom:0;height:22px;background:var(--band-red);border-top:3px solid var(--blue)}

  /* back */
  .watermark{position:absolute;left:40px;top:-40px;width:190px;height:190px;background:var(--faint);opacity:.8}
  .taglines{position:absolute;left:40px;bottom:38px;font-family:"Roboto",sans-serif;font-weight:500;font-size:38px;line-height:1;letter-spacing:-1px}
  .tagline--map{color:var(--green)}
  .tagline--ship{color:var(--sky)}
  .tagline--keep{color:var(--magenta)}
</style>
</head>
<body>
<main class="canvas">
  <section class="card card--front" aria-label="Business card front">
    <div class="brand">
      <span class="brand__mark"></span>
      <span class="brand__name">korvalit</span>
    </div>
    <div class="divider"></div>
    <div class="details">
      <p class="person__name">Maren Holloway</p>
      <p class="person__role">Business Development Manager</p>
      <p class="address">Level 1, 47 Fernby Street<br>Carlow Qld 4072</p>
      <ul class="contacts">
        <li><svg viewBox="0 0 12 12"><path fill="#c4252b" d="M2 1l2 0 1 3-1.3 1a7 7 0 0 0 3.3 3.3L8 7l3 1v2c0 .6-.4 1-1 1A9 9 0 0 1 1 2c0-.6.4-1 1-1z"/></svg>+61 (0)7 3840 5521</li>
        <li><svg viewBox="0 0 12 12"><path fill="#c4252b" d="M2 1l2 0 1 3-1.3 1a7 7 0 0 0 3.3 3.3L8 7l3 1v2c0 .6-.4 1-1 1A9 9 0 0 1 1 2c0-.6.4-1 1-1z"/></svg>+61 (0)7 3840 5538</li>
        <li><svg viewBox="0 0 12 12"><rect x="3" y="0.5" width="6" height="11" rx="1" fill="none" stroke="#c4252b" stroke-width="1.2"/></svg>+61 (0)412 604 287</li>
        <li><svg viewBox="0 0 12 12"><rect x="1" y="4" width="10" height="7" fill="#c4252b"/><rect x="3" y="1" width="6" height="3" fill="none" stroke="#c4252b"/></svg>+61 (0)7 3840 5500</li>
        <li><svg viewBox="0 0 12 12"><rect x="1" y="2" width="10" height="8" fill="#c4252b"/><path d="M1 2l5 4 5-4" fill="none" stroke="#fff"/></svg>mholloway@korvalit.com.au</li>
        <li><svg viewBox="0 0 12 12"><circle cx="6" cy="6" r="5.5" fill="#c4252b"/><path d="M1 6h10M6 .5c-3 3-3 8 0 11M6 .5c3 3 3 8 0 11" fill="none" stroke="#fff" stroke-width=".8"/></svg>www.korvalit.com.au</li>
      </ul>
    </div>
    <div class="band"></div>
  </section>

  <section class="card card--back" aria-label="Business card back">
    <div class="watermark"></div>
    <div class="taglines">
      <p class="tagline--map">MapOut</p>
      <p class="tagline--ship">ShipWell</p>
      <p class="tagline--keep">KeepSteady</p>
    </div>
  </section>
</main>
</body>
</html>
```